Brand new letterhead, business card, email signature etc.

We are a financial company in London, UK. Our website is www.marlowvane.com. We're wanting a complete remodel of the company colours, letter head, business cards, email signatures, etc. Looking to keep the same font for the company name. I have upload a colour palette that we want to work with. We're looking for company letterhead for outgoing letters/ correspondence, letterhead for internal documentation, email signatures, e-letters. etc. Ultimately we will redesign the entire website also. It is important that our clients get a strong, secure, warm, trustworthy, solid feeling and first impression.
Updates

Designs look the same

Target Market(s)

Institutional investors, (ultra) high net worth individuals

Industry/Entity Type

Finance, Invesments banking.

Font styles to use
Other font styles liked:
• Current font is "Champagne & Limousines"

Requirements
Must have
• Must use the colours provided on the PDF uploaded to the portal. The purple = main colour. The red = accent colour.
Nice to have
• Nice to use same font as now for the company name "Corvane". Font is "Champagne & Limousines". Nice to have some reference to the old logo flower, but only subtle.
Should not have
• Do not use the colour red from our website. Use the colours provided on the colour palette PDF that I uploaded in the portal.

```html
<!DOCTYPE html>
<html lang="en">
<head>
<meta charset="utf-8">
<title>Corvane Stationery</title>
<link rel="stylesheet" href="https://fonts.googleapis.com/css2?family=Didact+Gothic&family=Questrial&display=swap">
<style>
  :root {
    --backdrop: #d3d3d6;
    --ink: #141318;
    --accent: #d42c22;
    --accent-deep: #a8130f;
    --paper: #ffffff;
    --letter-paper: #f3f3f3;
    --footer-plum: #1e0c1c;
    --text-dark: #1c1a1f;
    --text-light: #f2f2f2;
    --side-mark: #26252b;
  }
  * { box-sizing: border-box; margin: 0; padding: 0; }
  html, body { width: 1200px; height: 792px; overflow: hidden; }
  body {
    position: relative;
    background: var(--backdrop);
    font-family: "Didact Gothic", "Century Gothic", sans-serif;
    color: var(--text-dark);
  }
  .sheet { position: absolute; }

  /* Shared name lockup: plain dot + name */
  .wordmark { display: flex; align-items: center; }
  .wordmark .dot { border-radius: 50%; background: var(--accent); flex: none; }
  .wordmark .name { font-family: "Questrial", sans-serif; font-weight: 400; letter-spacing: 0.02em; line-height: 1; }

  /* Business card — front */
  .card-front {
    left: 154px; top: 233px; width: 195px; height: 111px;
    background: var(--ink);
    border-bottom: 1px solid var(--accent);
  }
  .card-front .side-mark {
    position: absolute; left: 5px; top: 6px; height: 70px;
    writing-mode: vertical-rl; transform: rotate(180deg);
    font-family: "Questrial", sans-serif;
    font-size: 12px; color: var(--side-mark);
  }
  .card-front .person {
    position: absolute; right: 5px; top: 43px; text-align: right;
    padding-right: 3px; border-right: 2px solid var(--accent);
  }
  .person-name { font-family: "Questrial", sans-serif; font-weight: 700; }
  .person-name .given { color: var(--accent); }
  .card-front .person-name { font-size: 10.5px; color: var(--text-light); }
  .card-front .person-role { font-size: 4.8px; color: var(--text-light); margin-top: 1px; }
  .card-front .details {
    position: absolute; right: 5px; top: 67px; text-align: right;
    font-size: 4.6px; line-height: 7.2px; color: var(--text-light);
  }
  .card-front .details .gap { height: 3px; }
  .icon-dot { display: inline-block; width: 4px; height: 4px; border-radius: 50%; background: var(--accent); margin-left: 3px; vertical-align: middle; }

  /* Business card — back */
  .card-back {
    left: 379px; top: 233px; width: 194px; height: 111px;
    background: linear-gradient(90deg, #d42c22 0%, #d02a21 80%, var(--accent-deep) 100%);
    display: flex; align-items: center; justify-content: center;
  }
  .card-back .wordmark { gap: 8px; color: #f4d6d3; }
  .card-back .dot { width: 10px; height: 10px; background: #f4d6d3; }
  .card-back .name { font-size: 24px; }

  /* Email signature */
  .signature {
    left: 153px; top: 401px; width: 420px; height: 139px;
    background: var(--paper);
    border-bottom: 2px solid var(--accent);
  }
  .signature .wordmark { position: absolute; left: 22px; top: 55px; gap: 10px; color: var(--text-dark); }
  .signature .dot { width: 12px; height: 12px; }
  .signature .name { font-size: 28px; }
  .signature .divider { position: absolute; left: 210px; top: 22px; width: 1px; height: 94px; background: var(--text-dark); }
  .signature .person { position: absolute; left: 231px; top: 22px; }
  .signature .person-name { font-size: 14px; }
  .signature .person-role { font-size: 8px; margin-top: 1px; }
  .signature .address { margin-top: 9px; font-size: 8px; line-height: 10px; }
  .signature .contacts { margin-top: 8px; font-size: 8px; line-height: 10.2px; }
  .signature .contacts .icon-dot { margin: 0 5px 0 0; }

  /* Letterhead */
  .letterhead {
    left: 595px; top: 131px; width: 367px; height: 518px;
    background: var(--letter-paper);
  }
  .letterhead .wordmark { position: absolute; left: 0; top: 17px; width: 100%; justify-content: center; gap: 8px; color: var(--text-dark); }
  .letterhead .dot { width: 10px; height: 10px; }
  .letterhead .name { font-size: 24px; }
  .letterhead .footer {
    position: absolute; left: 0; bottom: 0; width: 100%; height: 42px;
    background: var(--footer-plum);
    border-top: 2px solid var(--accent);
    border-bottom: 1px solid var(--accent);
    display: flex; align-items: center; padding-left: 12px;
    color: var(--text-light); font-size: 7.4px; line-height: 10px;
  }
  .footer .col { display: flex; gap: 4px; align-items: flex-start; }
  .footer .col-phone { width: 103px; }
  .footer .col-web { width: 122px; }
  .footer svg { width: 7px; height: 20px; flex: none; }
</style>
</head>
<body>

  <section class="sheet card-front" aria-label="Business card front">
    <div class="side-mark">Corvane</div>
    <div class="person">
      <div class="person-name"><span class="given">Elena</span> Marwick</div>
      <div class="person-role">Managing Director</div>
    </div>
    <div class="details">
      48 Halden Row Suite 310<br>Easton, TX 75210
      <div class="gap"></div>
      (555) 204-3187<span class="icon-dot"></span><br>
      info@marlowvane.com<span class="icon-dot"></span><br>
      www.marlowvane.com<span class="icon-dot"></span>
    </div>
  </section>

  <section class="sheet card-back" aria-label="Business card back">
    <div class="wordmark"><span class="dot"></span><span class="name">Corvane</span></div>
  </section>

  <section class="sheet signature" aria-label="Email signature">
    <div class="wordmark"><span class="dot"></span><span class="name">Corvane</span></div>
    <div class="divider"></div>
    <div class="person">
      <div class="person-name"><span class="given">Elena</span> Marwick</div>
      <div class="person-role">Managing Director</div>
      <div class="address">48 Halden Row Suite<br>310 Easton, TX 75210</div>
      <div class="contacts">
        <div><span class="icon-dot"></span>(555) 204-3187</div>
        <div><span class="icon-dot"></span>info@marlowvane.com</div>
        <div><span class="icon-dot"></span>www.marlowvane.com</div>
      </div>
    </div>
  </section>

  <section class="sheet letterhead" aria-label="Letterhead">
    <div class="wordmark"><span class="dot"></span><span class="name">Corvane</span></div>
    <div class="footer">
      <div class="col col-phone">
        <svg viewBox="0 0 7 20" aria-hidden="true">
          <path d="M1.5 1.5c0 2.5 1.5 4 4 4l.8-1-1.3-.9-.6.5c-.8-.3-1.3-.9-1.6-1.6l.5-.6-.9-1.3z" fill="var(--accent)"/>
          <path d="M1.5 11.5c0 2.5 1.5 4 4 4l.8-1-1.3-.9-.6.5c-.8-.3-1.3-.9-1.6-1.6l.5-.6-.9-1.3z" fill="var(--accent)"/>
        </svg>
        <div>(555) 204-3187<br>(555) 204-3187</div>
      </div>
      <div class="col col-web">
        <svg viewBox="0 0 7 20" aria-hidden="true">
          <circle cx="3.5" cy="4" r="2.8" fill="var(--accent)"/>
          <rect x="0.7" y="12" width="5.6" height="4" fill="var(--accent)"/>
        </svg>
        <div>www.marlowvane.com<br>hello@marlowvane.com</div>
      </div>
      <div class="col col-address">
        <svg viewBox="0 0 7 20" aria-hidden="true">
          <path d="M3.5 9C1.5 6.3.8 5.1.8 3.8a2.7 2.7 0 0 1 5.4 0C6.2 5.1 5.5 6.3 3.5 9z" fill="none" stroke="var(--accent)" stroke-width="1"/>
          <circle cx="3.5" cy="3.8" r="0.9" fill="var(--accent)"/>
        </svg>
        <div>212 Fennick Lane,<br>Ashcombe, Kent, ME4 7QT</div>
      </div>
    </div>
  </section>

</body>
</html>
```